Book cover

I need a cover for a my 3rd book that kinda goes with my brand (my previous book. The name of my first book - "Turbulence Behind the Yoke" Hidden Strain Inside Modern Cockpits: A Guide for Travelers". In the same style I need my third book - NO HARBOR" to stand out. I need a bolder, less whimsy cover, less playful. So can we use some of the same elements to stay consistent in this book cover. Perhaps use text to envoke emotions. This is the back cover so far (see below attachemnent)

Hello,
Subject: Cover Direction & Brand Consistency

Hi everyone,

Here’s my honest take: I don’t think the current execution fully reflects my brand yet. What I’m wondering is whether we can bring more continuity across my books—borrowing elements from my first and second covers to inform this third one. Think of how authors like Dorian Welk maintain a recognizable style across their work. That consistency builds trust and signals authority before a reader even opens the book. Design choices like this matter more than we realize.

I’ve attached a cover I came across on Brindlemart that reminded me of Option 5 and feels aligned with where you’re headed. One thought: could we experiment with introducing a crack—or cracks—into the word HARBOR itself? Maybe put the title "NO HARBOR" at the edge of the cover vertically?

Curious to hear your thoughts and how you see this evolving.
P.s. Is there away to attach an idea?

NO HARBOR: Restoring Quiet Edges in a Culture that Praises Hurry

```html
<!DOCTYPE html>
<html lang="en">
<head>
<meta charset="utf-8">
<title>No Harbor – Book Cover</title>
<link rel="stylesheet" href="https://fonts.googleapis.com/css2?family=Inter:wght@800;900&family=Montserrat:wght@400;500;600&family=Oswald:wght@600&display=swap">
<style>
  :root {
    --ink-navy: #1b2533;
    --ink-deep: #0c1320;
    --sky-blue: #1fb5e8;
    --sky-mid: #2c6c9a;
    --sky-dark: #0f3356;
    --cloud: #d9e6f2;
    --white: #ffffff;
    --gold: #c9a24a;
  }
  * { margin: 0; padding: 0; box-sizing: border-box; }
  html, body { width: 1200px; height: 882px; overflow: hidden; background: var(--ink-navy); }
  .cover { position: relative; width: 1200px; height: 882px; overflow: hidden;
    background: linear-gradient(180deg, var(--ink-navy) 0%, #17202d 70%, var(--ink-deep) 100%);
    font-family: "Montserrat", sans-serif; color: var(--white); }

  /* Front artwork */
  .front-art { position: absolute; left: 570px; top: 0; width: 630px; height: 882px;
    background:
      radial-gradient(ellipse 260px 200px at 350px 70px, rgba(240,246,252,.95), rgba(200,222,240,.5) 55%, transparent 100%),
      radial-gradient(ellipse 360px 120px at 300px 440px, rgba(170,205,230,.55), transparent 80%),
      radial-gradient(ellipse 200px 140px at 620px 120px, rgba(190,215,235,.5), transparent 90%),
      linear-gradient(180deg, #6d9dc6 0%, var(--sky-mid) 35%, #1f5585 60%, var(--sky-dark) 85%, #0b2540 100%); }
  .spine-fade { position: absolute; left: 570px; top: 0; width: 70px; height: 882px;
    background: linear-gradient(90deg, var(--ink-navy) 0%, rgba(27,37,51,.6) 45%, rgba(27,37,51,0) 100%); }

  /* Back cover */
  .back-headline { position: absolute; left: 37px; top: 38px; width: 500px;
    font-weight: 600; font-size: 19.2px; line-height: 17.8px; color: var(--sky-blue); letter-spacing: .1px; }
  .back-copy { position: absolute; left: 37px; top: 124px; width: 485px;
    font-size: 12.2px; line-height: 17.7px; text-align: justify; }
  .author-bio { position: absolute; left: 37px; top: 551px; width: 377px;
    font-size: 10.4px; line-height: 12.7px; text-align: justify; }
  .author-bio p:last-child, .author-bio p:nth-child(2) { text-align: left; }
  .author-bio strong { font-weight: 600; letter-spacing: .4px; }
  .author-photo { position: absolute; left: 423px; top: 557px; width: 96px; height: 131px;
    background: radial-gradient(ellipse 60px 70px at 50% 25%, #3a3f47, #15181d 80%),
                linear-gradient(180deg, #2b2f35, #9a9ea5); }
  .publisher { position: absolute; left: 36px; top: 810px; display: flex; align-items: center; gap: 6px;
    font-size: 11px; font-weight: 600; letter-spacing: 1.6px; color: var(--gold); }
  .publisher .dot { width: 10px; height: 10px; border-radius: 50%; background: var(--gold); }
  .price { position: absolute; left: 212px; top: 816px; font-family: "Oswald", sans-serif;
    font-weight: 600; font-size: 10.5px; line-height: 14px; }

  /* Spine */
  .spine-title { position: absolute; left: 607px; top: 59px; transform-origin: 0 0; transform: rotate(90deg);
    white-space: nowrap; font-size: 13.6px; letter-spacing: .1px; }
  .spine-author { position: absolute; left: 607px; top: 625px; transform-origin: 0 0; transform: rotate(90deg);
    white-space: nowrap; font-size: 14px; font-weight: 500; }

  /* Front title */
  .front-title { position: absolute; left: 0; top: 0; font-family: "Inter", sans-serif; font-weight: 900;
    color: var(--white); letter-spacing: -6px; }
  .front-title span { position: absolute; left: 643px; font-size: 172px; line-height: 1; white-space: nowrap; }
  .front-title .t1 { top: 76px; }
  .front-title .t2 { top: 386px; }
  .front-title .t3 { top: 520px; }
  .front-subtitle { position: absolute; left: 648px; top: 730px; width: 540px;
    font-weight: 500; font-size: 30px; line-height: 31px; color: var(--sky-blue); }
</style>
</head>
<body>
<main class="cover">
  <div class="front-art" role="img" aria-label="Photograph of a jet airliner approaching head-on with landing gear down against a motion-streaked blue sky with clouds"></div>
  <div class="spine-fade"></div>

  <h2 class="back-headline">Women have been told we could do and be anything … and we can.<br>What’s rarely mentioned is the toll on our health, relationships, and overall wellbeing.</h2>

  <section class="back-copy">
    <p>Are you the woman who holds it all together—crushing deadlines, leading teams, raising a family—while quietly unraveling inside? Yes, you are competent and capable. You’ve simply been carrying more than you were ever meant to for too long.</p>
    <p>No Harbor offers a different way forward. Drawn from decades of experience flying commercial aircraft and championing women's health, retired Captain Marlowe Castellane reveals the missing skill most high-achieving women were never taught: protecting your margins in a world that glorifies overload. This vital buffer not only enables recovery after near-collapse, but also prevents you from reaching the breaking point of exhaustion.</p>
    <p>You will learn about the centuries-old mindset when humans first became cogs in the machine, the science of burnout and brain rewiring, the psychology driving us to push limits, and the cultural systems rigged against women. Discover how to spot the three stages of depletion before they ground you. Through self-assessment tools and actionable practices, the author guides us back home to ourselves by offering a roadmap to rebuild our strength, reconnect with joy and purpose, and redefine success to include true wellbeing.</p>
    <p>You don’t need to crash to earn a soft landing. Buckle up! No Harbor is your wakeup call to fly lighter and higher than you ever imagined.</p>
    <p>Marlowe Castellane is a speaker, consultant, and founder of the Crosswind Health Institute. With over 10,000 flight hours, she now empowers women to successfully lead without losing themselves.</p>
  </section>

  <section class="author-bio">
    <p><strong>CAPTAIN MARLOWE CASTELLANE</strong> is the founder of Clear Skies Wellness, an aviation-based wellbeing organization that builds on her 34+ years of experience as a commercial airline pilot. She helps others in high-performance professions and those seeking careers as airline pilots achieve a healthier, more rewarding life using practical techniques tailored for their careers. She currently captains wide-body aircrafts and has logged over 10,000 hours of jet flight time.</p>
    <p>Marlowe has over a decade of experience in health and wellbeing as an aviation strategist. She is certified in Mindfulness Based Stress Reduction (MBSR) at Halden University and earned a BS in Leadership (Sigma Lyra Tau) and an Executive Certificate in Business from Westmere College.</p>
    <p>Having travelled the globe repeatedly, Marlowe's favorite place in the world is with her family, spending time on the east and west coast of the US. She enjoys gardening, meditation, and the love of learning.</p>
  </section>
  <div class="author-photo" role="img" aria-label="Portrait of the author in captain's uniform standing beside a jet engine"></div>

  <div class="publisher"><span class="dot"></span>EMBER LANE PRESS</div>
  <div class="price">US $19.99<br>CA $23.99</div>

  <div class="spine-title">NO HARBOR: Restoring Quiet Edges in a Culture that Praises Hurry</div>
  <div class="spine-author">Capt. Marlowe Castellane</div>

  <h1 class="front-title"><span class="t1">NO</span><span class="t2">HAR</span><span class="t3">BOR:</span></h1>
  <p class="front-subtitle">Restoring Quiet Edges in a Culture that Praises Hurry</p>
</main>
</body>
</html>
```